Velmora Freightway Solutions Business cards

Would like a very unique design catchy but professional for business cards. Please use log provided.Marlon WellsCeo and Founder TransCon Logistix Solutions1-888-913-3225mwells@tlsolutionsus.comwww.tlsolutionsus.com

```html
<!DOCTYPE html>
<html lang="en">
<head>
<meta charset="utf-8">
<title>Velmora Freightway Solutions – Business Cards</title>
<link rel="stylesheet" href="https://fonts.googleapis.com/css2?family=Lato:wght@400;700&display=swap">
<style>
  :root {
    --backdrop: #e9e6e2;
    --navy: #0d2a45;
    --brand-blue: #1669b4;
    --band-blue: #1a76bf;
    --accent-red: #e3232c;
    --white: #ffffff;
  }
  * { margin: 0; padding: 0; box-sizing: border-box; }
  html, body {
    width: 1200px; height: 960px; overflow: hidden;
    background: var(--backdrop);
    font-family: "Lato", sans-serif;
  }
  .stage { position: relative; width: 1200px; height: 960px; }

  .card { position: absolute; border-radius: 26px; overflow: hidden; }

  .card-back {
    left: 237px; top: 47px; width: 720px; height: 405px;
    background: var(--navy);
    display: flex; flex-direction: column; align-items: center; justify-content: center;
  }
  .card-back .brand-name {
    color: var(--white); font-weight: 700; font-size: 42px; letter-spacing: 1px;
    margin-top: 10px;
  }
  .card-back .site {
    color: var(--white); font-size: 19px; letter-spacing: 2.5px; margin-top: 70px;
  }

  .card-front {
    left: 245px; top: 508px; width: 704px; height: 406px;
    background: var(--white);
  }
  .card-front .wave { position: absolute; left: 0; top: 0; }
  .card-front .brand-name {
    position: absolute; top: 110px; width: 100%; text-align: center;
    color: var(--brand-blue); font-weight: 700; font-size: 32px; letter-spacing: 1px;
  }
  .card-front .person-name {
    position: absolute; top: 208px; width: 100%; text-align: center;
    color: var(--brand-blue); font-weight: 700; font-size: 24px;
  }
  .card-front .person-title {
    position: absolute; top: 243px; width: 100%; text-align: center;
    color: var(--accent-red); font-size: 18px;
  }
  .contact {
    position: absolute; width: 100%; display: flex; justify-content: center; gap: 16px;
    color: var(--white); font-size: 17px;
  }
  .contact span { display: inline-flex; align-items: center; gap: 7px; }
  .contact-phone { top: 339px; }
  .contact-web { top: 368px; }
  .contact svg { width: 15px; height: 15px; }
</style>
</head>
<body>
<div class="stage">
  <section class="card card-back">
    <div class="brand-name">Velmora Freightway Solutions</div>
    <div class="site">www.vfwayroutes.com</div>
  </section>

  <section class="card card-front">
    <svg class="wave" width="704" height="406" viewBox="0 0 704 406">
      <path d="M0,200 Q250,318 585,297 L585,303 Q250,338 0,232 Z" fill="var(--navy)"/>
      <path d="M0,244 Q320,362 704,250 L704,406 L0,406 Z" fill="var(--band-blue)"/>
    </svg>
    <div class="brand-name">Velmora Freightway Solutions</div>
    <div class="person-name">DORIAN PIKE</div>
    <div class="person-title">CEO AND FOUNDER</div>
    <div class="contact contact-phone">
      <span>
        <svg viewBox="0 0 24 24"><path fill="#fff" d="M6.6 10.8a15 15 0 0 0 6.6 6.6l2.2-2.2a1 1 0 0 1 1-.25 11.4 11.4 0 0 0 3.6.57 1 1 0 0 1 1 1V20a1 1 0 0 1-1 1A17 17 0 0 1 3 4a1 1 0 0 1 1-1h3.5a1 1 0 0 1 1 1c0 1.25.2 2.45.57 3.57a1 1 0 0 1-.25 1z"/></svg>
        1-888-470-6158
      </span>
    </div>
    <div class="contact contact-web">
      <span>
        <svg viewBox="0 0 24 24"><rect x="3" y="6" width="18" height="13" rx="2" fill="#fff"/><path d="M4 8l8 6 8-6" stroke="var(--band-blue)" stroke-width="2" fill="none"/></svg>
        dpike@vfwayroutes.com
      </span>
      <span>
        <svg viewBox="0 0 24 24" fill="none" stroke="#fff" stroke-width="2"><circle cx="12" cy="12" r="9"/><path d="M3 12h18M12 3c3 3 3 15 0 18M12 3c-3 3-3 15 0 18"/></svg>
        www.vfwayroutes.com
      </span>
    </div>
  </section>
</div>
</body>
</html>
```